"Harbor Builders" is a residential building company and needs a new business card design and may re

We would like a redesign based on the existing logo, and would like to see a new font as well. We are bespoke home builders who build sustainable energy efficient homes.

Industry/Entity Type

Construction

Contact Information for Business Card

Business card size 40mm x 90mm

Colors

Designer to choose colors to be used in the design.

```html
<!DOCTYPE html>
<html lang="en">
<head>
<meta charset="utf-8">
<title>Harbor Builders – Business Card</title>
<link rel="stylesheet" href="https://fonts.googleapis.com/css2?family=Source+Sans+3:wght@400;600;700&display=swap">
<style>
  :root {
    --backdrop: #8e8f91;
    --card-light: #e6e6e8;
    --card-dark: #060607;
    --ink: #1c1c1e;
    --ink-soft: #4a4a4d;
    --rule: #3a3a3c;
    --accent: #a6c53a;
    --light-text: #e9e9ea;
  }
  * { margin: 0; padding: 0; box-sizing: border-box; }
  html, body {
    width: 1105px; height: 1200px; overflow: hidden;
    background: var(--backdrop);
    font-family: "Source Sans 3", "Myriad Pro", sans-serif;
  }
  .card {
    position: absolute; left: 182px; width: 747px; height: 427px;
  }
  .card--front { top: 119px; background: var(--card-light); color: var(--ink); }
  .card--back  { top: 636px; background: var(--card-dark); }

  .brand {
    position: absolute; display: flex; align-items: center; gap: 16px;
    font-weight: 600; line-height: 1; white-space: nowrap;
  }
  .brand__mark { display: block; flex: none; border: 8px solid var(--accent); }
  .card--front .brand { right: 42px; top: 50px; font-size: 42px; color: var(--ink); }
  .card--front .brand__mark { width: 52px; height: 52px; }
  .card--back .brand {
    left: 50%; top: 50%; transform: translate(-50%, -50%);
    font-size: 52px; color: var(--light-text); gap: 22px;
  }
  .card--back .brand__mark { width: 66px; height: 66px; border-width: 10px; }

  .contact-name {
    position: absolute; left: 30px; top: 245px;
    font-size: 26px; font-weight: 700; letter-spacing: 0.2px;
  }
  .contact-phone {
    position: absolute; left: 30px; top: 274px;
    font-size: 19px; color: var(--ink-soft);
  }
  .divider {
    position: absolute; left: 30px; right: 36px; top: 313px;
    height: 1.5px; background: var(--rule);
  }
  .contact-lines {
    position: absolute; left: 30px; top: 323px;
    font-size: 17px; line-height: 23px; color: var(--ink-soft);
  }
  .contact-lines .registry { font-size: 14px; font-stretch: condensed; }
  .contact-lines strong { font-weight: 700; color: var(--ink); }
  .company-address {
    position: absolute; right: 35px; top: 326px; text-align: right;
    font-size: 17px; line-height: 23px; color: var(--ink-soft);
  }
  .company-address strong { font-weight: 700; }
</style>
</head>
<body>
  <section class="card card--front">
    <div class="brand"><span class="brand__mark"></span>harbor builders</div>

    <div class="contact-name">Daniel Moretti</div>
    <div class="contact-phone">0400 555 218</div>
    <div class="divider"></div>

    <div class="contact-lines">
      <div>daniel@harborbuilders.com.au</div>
      <div>www.harborbuilders.com.au</div>
      <div class="registry"><strong>Registration:</strong> 40512 &nbsp;<strong>ABN:</strong> 12 345 678 901</div>
    </div>

    <div class="company-address">
      <div><strong>Harbor Builders Pty Ltd</strong></div>
      <div>PO Box 2740 Northgate</div>
      <div>LPO Eastvale WA 6000</div>
    </div>
  </section>

  <section class="card card--back">
    <div class="brand"><span class="brand__mark"></span>harbor builders</div>
  </section>
</body>
</html>
```